Small legal and financial translation company needs Squarespace website, brochure and logo

Hello,
We are Lumarin Services (www.lumarinservices-example.com), a boutique legal and financial translation company. We offer our services mainly to Spanish customers. Our primary line of business is the translation of financial statements, but we translate a wide variety legal and financial texts.
The project we are offering comprises three parts: a redo of the current website, an informational brochure for potential customer and a logo design. These three parts should provide a consistent image. We would develop content soon.
We are looking for a website that would look like a typical law firm website, nothing too fancy. Right now, it is in English, Spanish and French, although the new site need only be in English and Spanish. There must be good toggling between the English and Spanish versions. There would be no need for tie-ins to social media and it would not contain a blog. Basically, a static site. We aren't interesting in driving traffic to the site or SEO, as we will contact nearly all potential customers beforehand. The website must be built in Squarespace to enable a smooth transition. The content would be similar to the current page, we'll be working on the exact content, but a rough draft is attached.
The brochure will be some three pages and would introduce the company to potential customers, using similar images as the website and the logo to be designed.
The only specifications for the logo is, as the website and brochure, it convey a sense of security and trust.
Feel free to ask with any questions as this is the first time we have used this platform.
Thank you!
Updates

I've added a more or less final version for the text in the brochure and updated the brief. Added Wednesday, June 10, 2015

Target Market(s)

Spanish law firms, auditors, accountants, banks, investment firms

Industry/Entity Type

Finance

Logo Text

Lumarin Services

Number of Pages Required

5+ page

Font styles to use
Serif

Requirements
Must have
• The website must be built in Squarespace and have a good option to toggle between English and Spanish versions.
• Brochure must be in both English and Spanish, I'm attaching a rough draft of the information that it will probably have. This should give an idea about what to include and the spacing. I will update it to include the final information.
Nice to have
• Would be nice to have some quality finance- and legal-related images
Should not have
• Vibrant colours

```html
<!DOCTYPE html>
<html lang="en">
<head>
<meta charset="utf-8">
<title>Legal Translation — Lumarin Services</title>
<link rel="stylesheet" href="https://fonts.googleapis.com/css2?family=Cormorant+Garamond:wght@400;500&family=Montserrat:wght@400;600;700&display=swap">
<style>
  :root {
    --ink: #3a3a3a;
    --ink-dark: #1e1e1e;
    --muted: #9a9a9a;
    --accent: #2f6f6a;
    --brand: #a9dcef;
    --page: #ececec;
    --white: #ffffff;
    --band: #323232;
    --footer: #1f1f1f;
  }
  * { margin: 0; padding: 0; box-sizing: border-box; }
  html, body { width: 1200px; height: 1006px; overflow: hidden; background: var(--page); }
  body { position: relative; font-family: "Cormorant Garamond", Georgia, serif; color: var(--ink); }

  .hero {
    position: absolute; left: 0; top: 0; width: 1200px; height: 441px;
    background: radial-gradient(ellipse at 55% 60%, #6b6b6b 0%, #4a4a4a 40%, #2a2a2a 100%);
  }
  .brand {
    position: absolute; left: 16px; top: 22px;
    font-family: "Cormorant Garamond", Georgia, serif; font-weight: 500;
    font-size: 34px; line-height: 1; color: var(--brand); letter-spacing: 0.5px;
  }
  .main-nav { position: absolute; right: 18px; top: 52px; display: flex; gap: 27px; }
  .main-nav a {
    font-family: "Montserrat", Arial, sans-serif; font-weight: 600; font-size: 12px;
    letter-spacing: 1.3px; color: var(--white); text-decoration: none;
  }
  .hero-title {
    position: absolute; left: 0; width: 1224px; top: 195px; text-align: center;
    font-family: "Montserrat", Arial, sans-serif; font-weight: 700; font-size: 59px;
    letter-spacing: 2px; color: var(--white);
  }

  .section-nav { position: absolute; left: 180px; top: 523px; }
  .section-nav h2 { font-weight: 400; font-size: 21px; color: var(--accent); margin-bottom: 10px; }
  .section-nav ul { list-style: none; }
  .section-nav li {
    font-family: "Montserrat", Arial, sans-serif; font-size: 11.5px; letter-spacing: 1.6px;
    color: var(--muted); line-height: 15px; margin-bottom: 9px; text-transform: uppercase;
  }
  .section-nav li.current { color: var(--ink-dark); font-weight: 600; }

  .content { position: absolute; left: 404px; top: 523px; width: 620px; }
  .content h1 { font-weight: 400; font-size: 29px; letter-spacing: 0.8px; color: var(--ink); }
  .doc-list { display: flex; margin-top: 28px; }
  .doc-list ul { list-style: none; width: 320px; }
  .doc-list li { font-size: 19px; letter-spacing: 1px; line-height: 33.5px; color: var(--ink); }
  .doc-list li::before { content: "•"; margin: 0 8px 0 18px; }

  .footer-band { position: absolute; left: 0; top: 886px; width: 1200px; height: 56px; background: var(--band); }
  .footer { position: absolute; left: 0; top: 942px; width: 1200px; height: 64px; background: var(--footer); }
</style>
</head>
<body>
  <header class="hero" role="img" aria-label="Black and white photograph of a judge's gavel beside brass scales of justice">
    <div class="brand">Lumarin Services</div>
    <nav class="main-nav">
      <a href="#">HOME</a><a href="#">ENGLISH</a><a href="#">SPANISH</a>
    </nav>
    <div class="hero-title">LEGAL TRANSLATION</div>
  </header>

  <aside class="section-nav">
    <h2>English</h2>
    <ul>
      <li>Who we are</li>
      <li>Benefits</li>
      <li class="current">Legal translation</li>
      <li>Financial<br>translation</li>
      <li>Contact</li>
    </ul>
  </aside>

  <main class="content">
    <h1>Legal translation includes but is not limited to:</h1>
    <div class="doc-list">
      <ul>
        <li>all manner of deeds</li>
        <li>contracts</li>
        <li>due diligence</li>
        <li>bylaws</li>
        <li>expert reports</li>
        <li>lawsuits</li>
      </ul>
      <ul>
        <li>appeals</li>
        <li>loan agreements</li>
        <li>powers of attorney</li>
        <li>judgments and court orders</li>
        <li>M&amp;A agreements</li>
        <li>LBOs</li>
      </ul>
    </div>
  </main>

  <div class="footer-band"></div>
  <footer class="footer"></footer>
</body>
</html>
```